Business card design for a dynamic IT consulting company

We need a business card design for a young firm, specialized in the Telecommunications/Consulting industry. The name of the company is Quindor and Partners Business Consulting Ltd. (Short name: Quindor and Partnes)
Quindor = solve read reverse, so we aim to be uncomplicated and solution-oriented. The small pipe in our logo is also related to the word solve. So we need a new business card design, which is simple, eye catching and something non traditional (I would probably prefer a square shaped design rather than a rectangle, but open for suggestions). Attached our logo.

Target Market(s)

Usually our customers are Tier1 Telecoms providers (Q-Netra, Palorix, etc) and their executives.

Industry/Entity Type

Business

Contact Information for Business Card

Name: Bence Tolnavari
Email: b.tolnavari@quindor.hu
Web: www.quindor.hu
Mobile: +36 30 518 2769
Title: Managing Director

Optional:
Company name: Quindor and Partners Ltd.
Address: 1087 Budapest, Tolvenka str. 28/C, Hungary

Font styles to use
Other font styles liked:
• helveticaneue_medium, Prime Regular are used now.

Colors

Designer to choose colors to be used in the design.

Requirements
Must have
• I would like to have a 2 sided design.
Nice to have
• I thought if we make the logo a bit bigger (without the company name), that could go to the back with the company name below. I though, if the pipe in the logo is somehow touchable on the business card, would be nice and unique.

```html
<!DOCTYPE html>
<html lang="en">
<head>
<meta charset="utf-8">
<title>Quindor and Partners – Business Card</title>
<link href="https://fonts.googleapis.com/css2?family=Montserrat:wght@600&family=Work+Sans:wght@300;400&display=swap" rel="stylesheet">
<style>
  :root {
    --stage: #2a2a2a;
    --brand-blue: #1c9bd8;
    --brand-magenta: #b82a94;
    --paper: #ffffff;
    --ink: #555a5e;
    --ink-logo: #5d6166;
  }
  * { margin: 0; padding: 0; box-sizing: border-box; }
  html, body { width: 1200px; height: 930px; overflow: hidden; background: var(--stage); }
  .canvas { position: relative; width: 1200px; height: 930px; }

  .card {
    position: absolute;
    left: 278px;
    width: 645px;
    height: 369px;
    border-radius: 20px;
    overflow: hidden;
  }
  .card--front { top: 75px; background: var(--paper); }
  .card--back  { top: 486px; background: var(--brand-blue); }

  .card__wave { position: absolute; inset: 0; }

  .holder { position: absolute; left: 29px; top: 30px; color: var(--paper); }
  .holder__name {
    font-family: "Montserrat", sans-serif;
    font-weight: 600;
    font-size: 23px;
    letter-spacing: 0.3px;
    line-height: 1;
  }
  .holder__title {
    font-family: "Work Sans", sans-serif;
    font-weight: 300;
    font-size: 16px;
    margin-top: 4px;
  }

  .brand {
    position: absolute;
    display: flex;
    align-items: center;
    gap: 10px;
    font-family: "Work Sans", sans-serif;
    font-weight: 400;
    white-space: nowrap;
  }
  .brand__mark { display: block; }
  .brand--front { right: 27px; top: 136px; color: var(--ink-logo); font-size: 30px; }
  .brand--front .brand__mark { width: 14px; height: 14px; background: var(--brand-magenta); }
  .brand--back {
    left: 0; right: 0; top: 155px;
    justify-content: center;
    color: var(--paper);
    font-size: 46px;
  }
  .brand--back .brand__mark { width: 20px; height: 20px; background: var(--paper); }

  .divider {
    position: absolute;
    left: 29px; right: 27px; top: 250px;
    height: 1px;
    background: var(--brand-blue);
  }

  .contacts {
    position: absolute;
    left: 29px; top: 276px;
    list-style: none;
    font-family: "Work Sans", sans-serif;
    font-weight: 300;
    font-size: 16px;
    color: var(--ink);
    line-height: 20px;
  }
  .contacts li { display: flex; align-items: center; gap: 10px; }
  .contacts svg { width: 12px; height: 12px; flex: none; }

  .address {
    position: absolute;
    right: 27px; top: 296px;
    text-align: right;
    font-family: "Work Sans", sans-serif;
    font-weight: 300;
    font-size: 16px;
    line-height: 20px;
    color: var(--ink);
    font-style: normal;
  }
</style>
</head>
<body>
<main class="canvas">

  <section class="card card--front">
    <svg class="card__wave" viewBox="0 0 645 369" width="645" height="369" aria-hidden="true">
      <path d="M0 106 C90 150 200 148 305 100 C430 42 545 12 645 56 V50 C545 6 430 18 300 85 C200 135 85 140 0 96 Z" fill="var(--brand-magenta)"/>
      <path d="M0 0 H645 V47 C545 4 430 14 298 80 C198 128 85 133 0 90 Z" fill="var(--paper)"/>
      <path d="M0 0 H645 V44 C545 0 430 10 296 76 C196 124 85 128 0 86 Z" fill="var(--brand-blue)"/>
    </svg>

    <div class="holder">
      <h1 class="holder__name">Bence Tolnavari</h1>
      <p class="holder__title">Managing Director</p>
    </div>

    <div class="brand brand--front">
      <span class="brand__mark"></span>
      <span class="brand__name">Quindor &amp; Partners</span>
    </div>

    <div class="divider"></div>

    <ul class="contacts">
      <li>
        <svg viewBox="0 0 12 12"><path d="M3 1 L5 3.5 L4 5 C4.6 6.4 5.6 7.4 7 8 L8.5 7 L11 9 L9.8 10.8 C5.5 10.6 1.4 6.5 1.2 2.2 Z" fill="none" stroke="var(--brand-blue)" stroke-width="1.1" stroke-linejoin="round"/></svg>
        <span>+36 30 518 2769</span>
      </li>
      <li>
        <svg viewBox="0 0 12 12"><rect x="1" y="2.5" width="10" height="7" fill="none" stroke="var(--brand-blue)" stroke-width="1.1"/><path d="M1 2.5 L6 6.5 L11 2.5" fill="none" stroke="var(--brand-blue)" stroke-width="1.1"/></svg>
        <span>b.tolnavari@quindor.hu</span>
      </li>
      <li>
        <svg viewBox="0 0 12 12"><circle cx="6" cy="6" r="5" fill="none" stroke="var(--brand-blue)" stroke-width="1"/><ellipse cx="6" cy="6" rx="2.2" ry="5" fill="none" stroke="var(--brand-blue)" stroke-width="1"/><path d="M1 6 H11 M2 3.5 H10 M2 8.5 H10" stroke="var(--brand-blue)" stroke-width="0.9"/></svg>
        <span>www.quindor.hu</span>
      </li>
    </ul>

    <address class="address">1087 Budapest,<br>Tolvenka str. 28/C, Hungary</address>
  </section>

  <section class="card card--back">
    <div class="brand brand--back">
      <span class="brand__mark"></span>
      <span class="brand__name">Quindor &amp; Partners</span>
    </div>
  </section>

</main>
</body>
</html>
```